A website for Kovadrel Limited

We need a new and modern website for our company. We are engineering consultants and contractors (EPC) in the oil and gas industry and building services industry.
What we do:
Engineering, procurement, construction
Automation (safety and process)
Non-destructive testing
Training
We have an existing website and the content can be referred from there since we are remaking the website
For more information visit Kovadrel Limited Kenya

```html
<!DOCTYPE html>
<html lang="en">
<head>
<meta charset="utf-8">
<title>Kovadrel Limited</title>
<link href="https://fonts.googleapis.com/css2?family=Poppins:wght@400;500;600;700&display=swap" rel="stylesheet">
<style>
:root{
  --rust:#a3402b;
  --rust-soft:#c66a55;
  --orange:#e06a3c;
  --ink:#1d1d1d;
  --black:#0c0605;
  --white:#ffffff;
  --hero-a:#8a6248;
  --hero-b:#c9a27f;
}
*{margin:0;padding:0;box-sizing:border-box}
html,body{width:1200px;height:3234px;overflow:hidden}
body{font-family:'Poppins',sans-serif;background:var(--white);color:var(--ink);position:relative}
.abs{position:absolute}
.upper{text-transform:uppercase}

.site-header{left:0;top:0;width:1200px;height:82px;background:var(--white)}
.brand{display:flex;align-items:center;gap:8px;font-weight:400;color:var(--rust-soft);font-size:19px;line-height:1.1}
.brand-dot{width:60px;height:60px;border-radius:50%;border:2px solid var(--rust-soft);flex:none}
.site-header .brand{position:absolute;left:370px;top:11px}
.menu-toggle{left:1005px;top:26px;width:36px}
.menu-toggle span{display:block;height:4px;background:var(--rust);border-radius:2px;margin-bottom:8px}

.hero{left:0;top:82px;width:1200px;height:544px;overflow:hidden}
.hero-photo{position:absolute;inset:0;background:linear-gradient(120deg,var(--hero-a),var(--hero-b) 60%,#6e4a36)}
.hero-title{position:absolute;left:100px;top:160px;width:370px;text-align:center;color:var(--white);font-weight:700;font-size:58px;line-height:76px}

.section-title{font-weight:700;font-size:34px;line-height:1.2}
.body-copy{font-weight:600;font-size:15.5px;line-height:30px}
.btn{display:inline-block;width:174px;height:52px;line-height:52px;text-align:center;font-weight:600;font-size:19px}
.btn-rust{background:var(--rust);color:var(--white)}
.btn-white{background:var(--white);color:var(--rust)}

.photo-disc{border-radius:50%;position:absolute}

.history{left:0;top:626px;width:1200px;height:567px}
.history .section-title{position:absolute;left:113px;top:132px;color:var(--rust)}
.history .body-copy{position:absolute;left:113px;top:192px;width:410px}
.history .btn{position:absolute;left:112px;top:398px}

.about{left:0;top:1193px;width:1200px;height:575px;background:var(--rust);overflow:hidden}
.about .section-title{position:absolute;left:638px;top:92px;color:var(--white)}
.about .body-copy{position:absolute;left:641px;top:157px;width:460px;color:var(--white)}
.about .btn{position:absolute;left:638px;top:426px}

.services{left:0;top:1768px;width:1200px;height:654px;overflow:hidden}
.services .section-title{position:absolute;left:0;width:1200px;top:92px;text-align:center;color:var(--rust)}
.service{position:absolute;width:248px;height:248px;border-radius:50%;display:flex;align-items:center;justify-content:center;text-align:center;color:var(--white);font-weight:600;font-size:13px;line-height:30px;padding:20px}

.vision{left:0;top:2422px;width:1200px;height:353px;background:linear-gradient(90deg,#b24f38,#c0604a 50%,#b24f38);text-align:center;color:var(--white)}
.vision .section-title{position:absolute;left:0;width:1200px;top:78px}
.vision .body-copy{position:absolute;left:0;width:1200px;top:148px}
.vision .btn{position:absolute;left:513px;top:210px}

.site-footer{left:0;top:2775px;width:1200px;height:459px;background:var(--black);color:var(--white);overflow:hidden}
.site-footer .brand{position:absolute;left:134px;top:170px;color:var(--white)}
.site-footer .brand-dot{border-color:var(--white);width:66px;height:66px}
.footer-col{position:absolute;top:48px}
.footer-col h3{font-weight:600;font-size:18px;margin-bottom:22px}
.footer-col li{list-style:none;font-weight:600;font-size:15px;line-height:30px}
.contact-row{position:absolute;left:840px;display:flex;gap:16px;font-weight:600;font-size:15px;line-height:30px}
.contact-row svg{flex:none;margin-top:6px}
.footer-rule{left:238px;top:400px;width:962px;height:1px;background:#3a2a26}
.copyright{left:388px;top:418px;font-weight:600;font-size:13px}
</style>
</head>
<body>

<header class="site-header abs">
  <div class="brand"><span class="brand-dot"></span><span>Kovadrel<br>Limited</span></div>
  <div class="menu-toggle abs" aria-label="Menu"><span></span><span></span><span></span></div>
</header>

<section class="hero abs">
  <div class="hero-photo" role="img" aria-label="Engineers in hard hats reviewing plans on a worktable"></div>
  <svg class="abs" style="left:0;top:0" width="1200" height="544">
    <path d="M0 -82 C330 -82 490 120 490 270 C490 440 330 544 0 544 Z" fill="#c4654d" opacity=".9"/>
    <path d="M0 -82 C330 -82 490 120 490 270" fill="none" stroke="#e9a07f" stroke-width="6"/>
    <path d="M0 0 C180 80 180 400 0 470" fill="none" stroke="#f3d0c2" stroke-width="1.5"/>
  </svg>
  <h1 class="hero-title upper">Kovadrel Limited</h1>
</section>

<section class="history abs">
  <svg class="abs" style="left:0;top:0" width="1200" height="567">
    <polygon points="772,0 1200,0 1200,567 832,567 607,300" fill="var(--rust)"/>
    <polyline points="1200,40 1060,285 1200,445" fill="none" stroke="#e3a592" stroke-width="1.5"/>
  </svg>
  <div class="photo-disc" style="left:618px;top:71px;width:426px;height:426px;border:6px solid #fff;background:radial-gradient(circle at 65% 55%,#b8c6ea,#2a3556 40%,#12172a)" role="img" aria-label="Welder at work with sparks flying"></div>
  <h2 class="section-title upper">History</h2>
  <p class="body-copy upper">Kovadrel was incorporated in 2010 with the huge potential of the LPG and petroleum market in Eastern and Central Africa in mind. We have provided and continue to provide the LPG and petroleum technical industry with innovative and cost-effective services.</p>
  <a class="btn btn-rust upper">Read More</a>
</section>

<section class="about abs">
  <svg class="abs" style="left:0;top:0" width="1200" height="575">
    <polygon points="0,0 355,0 290,575 0,575" fill="#d99a86"/>
    <polyline points="0,40 150,290 0,540" fill="none" stroke="#f1cdbf" stroke-width="1.5"/>
  </svg>
  <div class="photo-disc" style="left:133px;top:68px;width:430px;height:430px;border:6px solid #fff;background:linear-gradient(135deg,#2b2b2b,#8d8d8d 45%,#b0303a 55%,#3a3a3a)" role="img" aria-label="Industrial pipework and structural steel"></div>
  <h2 class="section-title upper">Who We Are</h2>
  <p class="body-copy upper">Kovadrel undertakes design, supply, installation and commissioning of LPG and petroleum systems including LPG reticulated systems (piped gas). We also do LPG tank revalidation and recertification. Our clients include: oil companies (both multinationals and local), government agencies, manufacturing companies, agricultural institutions, and the building services industry.</p>
  <a class="btn btn-white upper">Read More</a>
</section>

<section class="services abs">
  <svg class="abs" style="left:0;top:0" width="1200" height="654">
    <polygon points="0,0 226,0 399,315 163,654 0,654" fill="var(--rust)"/>
    <polyline points="0,0 178,330 0,480" fill="none" stroke="#e3a592" stroke-width="1.5"/>
  </svg>
  <h2 class="section-title upper">What We Do</h2>
  <div class="service upper" style="left:114px;top:188px;border:5px solid #fff;background:radial-gradient(circle,#5a3a2c,#2a1f1b)" role="img" aria-label="Engineering plant equipment">Engineering, procurement,<br>construction</div>
  <div class="service upper" style="left:393px;top:188px;border:5px solid var(--rust);background:radial-gradient(circle,#6b4a4e,#2c2838)" role="img" aria-label="Process plant at dusk">Automation<br>(safety and process)</div>
  <div class="service upper" style="left:672px;top:188px;border:5px solid var(--rust);background:linear-gradient(180deg,#2c3f70,#5a5a3a 60%,#c9a53a)" role="img" aria-label="Row of gas cylinders">Non-destructive<br>testing</div>
  <div class="service upper" style="left:949px;top:173px;border:5px solid var(--rust);background:radial-gradient(circle,#7a7870,#3a3c38)" role="img" aria-label="Trainees in a classroom session">Training</div>
</section>

<section class="vision abs" role="img" aria-label="Team working together, tinted rust">
  <h2 class="section-title upper">Our Vision</h2>
  <p class="body-copy upper">To be a world class provider of petroleum technical expertise.</p>
  <a class="btn btn-white upper">Read More</a>
</section>

<footer class="site-footer abs">
  <svg class="abs" style="left:0;top:0" width="1200" height="459">
    <polygon points="0,0 238,0 200,459 0,459" fill="var(--rust)"/>
    <polyline points="0,240 165,56 0,-80" fill="none" stroke="#d78a74" stroke-width="1.5"/>
    <polyline points="263,52 352,232 228,418" fill="none" stroke="var(--orange)" stroke-width="16"/>
  </svg>
  <div class="brand"><span class="brand-dot"></span><span>Kovadrel<br>Limited</span></div>
  <div class="footer-col" style="left:364px">
    <h3 class="upper">Quick Links</h3>
    <ul class="upper">
      <li>Home</li><li>About Us</li><li>Services</li><li>Products</li><li>Our Projects</li><li>Our Clients</li><li>Where We Operate</li><li>Our Partners</li><li>Contacts</li>
    </ul>
  </div>
  <div class="footer-col" style="left:616px">
    <h3 class="upper">About</h3>
    <ul class="upper"><li>Kovadrel's core<br>business is<br>engineering works<br>(oil and gas<br>engineering).</li></ul>
  </div>
  <div class="footer-col" style="left:885px"><h3 class="upper">Follow Us</h3></div>
  <div class="contact-row" style="top:100px">
    <svg width="24" height="24" viewBox="0 0 24 24"><path d="M6.6 10.8a15 15 0 0 0 6.6 6.6l2.2-2.2c.3-.3.7-.4 1-.2 1.1.4 2.3.6 3.6.6.6 0 1 .4 1 1V20c0 .6-.4 1-1 1C10.6 21 3 13.4 3 4c0-.6.4-1 1-1h3.5c.6 0 1 .4 1 1 0 1.3.2 2.5.6 3.6.1.3 0 .7-.2 1z" fill="#fff"/></svg>
    <span>+254 700 555 123 |<br>+254 700 555 456</span>
  </div>
  <div class="contact-row" style="top:184px">
    <svg width="24" height="18" viewBox="0 0 24 18"><rect x="1" y="1" width="22" height="16" rx="2" fill="#fff"/><path d="M2 2l10 8 10-8" fill="none" stroke="#0c0605" stroke-width="2"/></svg>
    <span class="upper">info@kovadrel.co.ke</span>
  </div>
  <div class="contact-row" style="top:245px">
    <svg width="24" height="24" viewBox="0 0 24 24"><path d="M12 2a7 7 0 0 0-7 7c0 5 7 13 7 13s7-8 7-13a7 7 0 0 0-7-7zm0 9.5a2.5 2.5 0 1 1 0-5 2.5 2.5 0 0 1 0 5z" fill="#fff"/></svg>
    <span class="upper">Harlow Court, Suite B12,<br>Kitengela Road</span>
  </div>
  <div class="footer-rule abs"></div>
  <p class="copyright abs upper">Copyright © 2023 Kovadrel Limited all rights reserved.</p>
</footer>

</body>
</html>
```